Need App for Impact Related Events

My app is to help with internal events. When you enter the prompted event code the next screen shows you everyone currently at the event. It will give you the ability to Start a conversation with someone you met at that event, or signal it is your turn to send a message. The next screen is a message thread with that person. I am looking for a design that incorporates the colors and ‘feel good’ emotion of our logo. I have pieced together a pretty good interpretation of what I’m looking for in the attached mockup by slicing and dicing designs. I also attached our logo mascot.Screens (see attached mockups)

Note 1: I do not like the picture on the screen used in screen one because it makes it seem like a dating app. I attached an alternative photo that can be used or present different ideas.

Note 2: On the login/signup screen (screen 2) I need an additional first and last name for login, you can try to fit this on one login screen or present a two step signup screen where that is presented in the second screen.

READ MOCKUP GUIDELINES UNDER Must Haves

Target Market(s)

People attending internal social impact events

Industry/Entity Type

Charity

Font styles to use
Sans Serif

Colors
86cfc6

Requirements
Must have
• Follow the screen mockups attached to project
• PLEASE READ
• I have provided a relatively close design of what I’m looking for in the mockups. Some screens need to be followed more closely to my design mockup than other. I have listed a guide below how how closely you should follow my mockup design exactly. Overall I would like to see some ideas of incorporating a few accent colors so it doesn’t appear SO Blue. I also attached some app inspiration designs I found from around the web
• Screen Mockup Guideline Follow %
• Screen 1: 65% - mostly on target, would like to see ways to make it not SO Blue and possibly creative places to add some explainer text describing the app
• Screen 2: 50% - general design idea is here, but more open
• Screen 3: 35% - a lot more room for design influence
• Screen 4: 70% - mostly on target, a little room for design influence/color scheme ideas
• Screen 5-6: 25% - a lot of room for design change/ideas/influence
• Screen 7-8: 80% - already very close to what I need, maybe open to slight sizing and color scheme ideas
• Screen 9: 15% - the most open for influence, only the general functionality of the screen is communicated here
Nice to have
• Please Read Mockup Guideline above. In large part I am looking for something to use some nice accent colors so it is not overwhelmingly blue and bring the whole design into a seamless style.
Should not have

```html
<!DOCTYPE html>
<html lang="en">
<head>
<meta charset="utf-8">
<title>Impact Related Events</title>
<link rel="stylesheet" href="https://fonts.googleapis.com/css2?family=Montserrat:wght@500;600;700&display=swap">
<style>
  :root {
    --page-bg: #eceef1;
    --teal: #19c6c4;
    --teal-soft: #8fe3df;
    --ink-dark: #2f2520;
    --muted-text: #c3c5ca;
    --label-grey: #9a9ca1;
    --line-grey: #cfd2d6;
    --screen-bg: #ffffff;
    --photo-top: #2f6f9e;
    --photo-mid: #7fa9c4;
    --social-blue: #1b7fd6;
    --social-sky: #1fa2e8;
  }
  * { box-sizing: border-box; margin: 0; padding: 0; }
  html, body { width: 1200px; height: 1105px; overflow: hidden; }
  body {
    background: var(--page-bg);
    font-family: "Montserrat", sans-serif;
    position: relative;
  }

  /* Left presentation column */
  .brand-mark {
    position: absolute; left: 44px; top: 560px;
    display: flex; align-items: center; gap: 16px;
  }
  .brand-dot {
    width: 64px; height: 64px; border-radius: 50%;
    background: var(--teal);
  }
  .brand-name {
    font-weight: 700; font-size: 34px; color: var(--ink-dark);
  }
  .project-title {
    position: absolute; left: 44px; top: 748px;
    font-size: 33px; font-weight: 600; color: var(--teal);
    letter-spacing: -0.2px;
  }
  .project-summary {
    position: absolute; left: 57px; top: 838px; width: 548px;
    font-size: 20px; font-weight: 600; line-height: 32px;
    color: var(--muted-text);
  }

  /* Phone screen, flat */
  .app-screen {
    position: absolute; left: 660px; top: 40px;
    width: 440px; height: 900px; border-radius: 44px;
    background: var(--screen-bg); overflow: hidden;
    box-shadow: 0 30px 60px rgba(60, 70, 90, 0.18);
  }
  .hero-photo {
    position: absolute; left: 0; top: 0; width: 100%; height: 560px;
    background: linear-gradient(180deg, var(--photo-top) 0%, var(--photo-mid) 48%, rgba(255,255,255,0) 100%);
  }
  .hero-brand {
    position: absolute; top: 170px; left: 0; width: 100%;
    display: flex; flex-direction: column; align-items: center; gap: 14px;
  }
  .hero-brand .brand-dot { width: 84px; height: 84px; }
  .hero-brand .brand-name { color: #ffffff; font-size: 30px; }

  .login-button, .register-button {
    position: absolute; left: 80px; width: 280px; height: 66px;
    border-radius: 33px; border: none;
    font-family: "Montserrat", sans-serif; font-weight: 700;
    display: flex; align-items: center; justify-content: center;
  }
  .login-button {
    top: 560px; background: var(--teal); color: #ffffff;
    font-size: 14px; letter-spacing: 1px;
    box-shadow: 0 10px 24px rgba(25, 198, 196, 0.45);
  }
  .register-button {
    top: 652px; background: #ffffff; color: var(--teal);
    font-size: 15px;
    box-shadow: 0 8px 22px rgba(25, 198, 196, 0.28);
  }

  .social-divider {
    position: absolute; top: 760px; left: 40px; width: 360px;
    display: flex; align-items: center; gap: 14px;
  }
  .social-divider .rule { flex: 1; height: 1px; background: var(--line-grey); }
  .social-divider .label { font-size: 12px; font-weight: 600; color: var(--label-grey); }

  .social-row {
    position: absolute; top: 800px; left: 0; width: 100%;
    display: flex; justify-content: center; gap: 40px;
  }
  .social-button { display: flex; align-items: center; gap: 8px; }
  .social-button .dot { width: 34px; height: 34px; border-radius: 50%; }
  .social-button.linkup .dot { background: var(--social-blue); }
  .social-button.chirper .dot { background: var(--social-sky); }
  .social-button .name { font-size: 13px; font-weight: 600; color: var(--label-grey); }
</style>
</head>
<body>

  <div class="brand-mark">
    <span class="brand-dot"></span>
    <span class="brand-name">Kindly Hive</span>
  </div>
  <h1 class="project-title">Impact Related Events</h1>
  <p class="project-summary">app is to help with internal events. When you enter the prompted event code the next screen shows you everyone currently at the event. It will give you the ability to Start a conversation with someone you met at that event, or signal it is your turn to send a message. The next screen is a message thread with that person.</p>

  <section class="app-screen">
    <div class="hero-photo" role="img" aria-label="Photo of two smiling event attendees outdoors under a blue sky, fading into white"></div>
    <div class="hero-brand">
      <span class="brand-dot"></span>
      <span class="brand-name">Kindly Hive</span>
    </div>

    <button class="login-button">LOGIN</button>
    <button class="register-button">Register Now</button>

    <div class="social-divider">
      <span class="rule"></span>
      <span class="label">Login with Social</span>
      <span class="rule"></span>
    </div>
    <div class="social-row">
      <div class="social-button linkup"><span class="dot"></span><span class="name">Linkup</span></div>
      <div class="social-button chirper"><span class="dot"></span><span class="name">Chirper</span></div>
    </div>
  </section>

</body>
</html>
```